Business Card - Tidal Lanes

Need Business Card design for company named Tidal Lanes. Software development focused mainly on Brindle Orvix & Zelt Apps. I've attached our logo with both a black and white background. Please add trademark symbol to logo when using.

```html
<!DOCTYPE html>
<html lang="en">
<head>
<meta charset="utf-8">
<title>Tidal Lanes – Business Card</title>
<link rel="stylesheet" href="https://fonts.googleapis.com/css2?family=Open+Sans:wght@400;600;700&display=swap">
<style>
  :root {
    --stage: #e9e9ee;
    --card-black: #050505;
    --orange-deep: #fb9a36;
    --orange-core: #f9c21a;
    --gold: #f5b400;
    --amber: #f08a1e;
    --red: #d9261c;
    --white: #ffffff;
    --rule: #6d6d6d;
  }
  * { box-sizing: border-box; margin: 0; padding: 0; }
  html, body {
    width: 1200px; height: 987px; overflow: hidden;
    background: var(--stage);
    font-family: "Open Sans", Arial, sans-serif;
  }
  .canvas {
    width: 1200px; height: 987px;
    display: flex; flex-direction: column; align-items: center; justify-content: center;
    gap: 56px;
  }
  .card {
    width: 760px; height: 434px;
    border-radius: 34px;
    position: relative;
    overflow: hidden;
    box-shadow: 0 10px 28px rgba(0,0,0,.18);
  }

  /* Front */
  .card--front { background: var(--card-black); color: var(--white); }
  .brand {
    position: absolute; left: 0; right: 0; top: 96px;
    display: flex; align-items: center; justify-content: center; gap: 16px;
  }
  .brand__dot { width: 34px; height: 34px; border-radius: 50%; background: var(--gold); }
  .brand__name { font-size: 50px; font-weight: 700; letter-spacing: -1px; color: var(--white); }
  .brand__tm { font-size: 16px; font-weight: 700; vertical-align: top; margin-left: 2px; }
  .divider {
    position: absolute; left: 60px; right: 60px; top: 200px; height: 2px;
    background: linear-gradient(90deg, transparent, var(--rule) 20%, #9a9a9a 50%, var(--rule) 80%, transparent);
  }
  .contact {
    position: absolute; left: 0; right: 0; top: 226px;
    text-align: center; font-size: 24px; line-height: 1.55;
  }
  .contact__name { color: var(--gold); font-weight: 700; }
  .contact__title { color: var(--white); font-weight: 400; }
  .contact__phones { display: flex; justify-content: center; align-items: center; gap: 12px; }
  .icon { width: 20px; height: 20px; fill: var(--gold); }

  /* Back */
  .card--back {
    background: radial-gradient(circle at 48% 50%, var(--orange-core) 0%, #fbac2a 40%, var(--orange-deep) 80%);
    color: var(--white);
  }
  .back__brand {
    position: absolute; left: 0; right: 0; top: 150px;
    display: flex; align-items: center; justify-content: center; gap: 16px;
  }
  .back__dot { width: 34px; height: 34px; border-radius: 50%; background: var(--white); }
  .back__name { font-size: 50px; font-weight: 700; letter-spacing: -1px; }
  .back__url {
    position: absolute; left: 0; right: 0; top: 300px;
    text-align: center; font-size: 24px; letter-spacing: 2px;
  }
</style>
</head>
<body>
<main class="canvas">
  <section class="card card--front" aria-label="Business card front">
    <div class="brand">
      <span class="brand__dot"></span>
      <span class="brand__name">Tidal Lanes<span class="brand__tm">™</span></span>
    </div>
    <div class="divider"></div>
    <div class="contact">
      <p><span class="contact__name">Your Name,</span> <span class="contact__title">Title</span></p>
      <p>4120 Cedar Row, Marrow Bay, FL 33500</p>
      <p class="contact__phones">
        <svg class="icon" viewBox="0 0 20 20" aria-hidden="true"><rect x="5" y="1" width="10" height="18" rx="2"/><rect x="7" y="4" width="6" height="8" fill="#050505"/></svg>
        <span>555-214-7730</span>
        <svg class="icon" viewBox="0 0 20 20" aria-hidden="true"><path d="M4 2c1-1 2-1 3 0l2 3c.5 1 0 2-1 2.5 1 2 2.5 3.5 4.5 4.5.5-1 1.5-1.5 2.5-1l3 2c1 1 1 2 0 3l-1.5 1.5C14 19 1 6 2.5 3.5z"/></svg>
        <span>555-608-1942</span>
      </p>
    </div>
  </section>

  <section class="card card--back" aria-label="Business card back">
    <div class="back__brand">
      <span class="back__dot"></span>
      <span class="back__name">Tidal Lanes</span>
    </div>
    <p class="back__url">www.tidallanes.com</p>
  </section>
</main>
</body>
</html>
```